LB - WESITE NEEDED PAGE: Clean / Modern / Pro & Dynamic

Lantern-Brokers is a new insurance brokerage firm dealing exclusively with companies (BToB) providing the following property: Liabilities Insurance Insurances Automobile Insurance Insurances Construction% 26amp; Engineering Casualty Workmen 's Compensation Health Insurance Marime% 26amp; Transit Credit Insurance Young, Fast, Proactive and Dynamic we call ourselves Lantern-Brokers because we are a "start-up" willing to make a difference in the market, bringing modernity and speed to our industry, still too bureaucratic / procedural / opaque uninitiated. We need something respecting the colors of our orange logtype; blue; white; black; easy to scroll, with simple information on the company; - who we are - our team (with the pictures) - what we do - what we do - contact us, contact us (google map) Luanda (Angola) Small company, just need something flashy / professional / structured / modern.

Target Market(s)

BtoB; Oil and gas companies; French speaking copying established in Angola, all industrials, factories and importers of goods.

Industry/Entity Type

Insurance Broker

Font styles to use
Sans Serif

Colors

Designer to choose colors to be used in the design.

Requirements
Must have
• We need something respecting the colors of our orange logtype; blue; white; black; easy to scroll, with simple information on the company; - who we are - our team (with the pictures) - what we do - what we do - contact us, contact us (google map) Luanda (Angola) Small company, just need something flashy / professional / structured / modern.
Nice to have
• A page format
Should not have
• WE DO NOT WANT A REFER TO OUR LOGO, but a Home Page for our Website with the basics categories ... >> PLEASE CAREFULLY USE THE RIGHT COLOR OF THE LOGOTYPE which are the ones enclosed Orange / Turquoise / Black as per the business card .

```html
<!DOCTYPE html>
<html lang="en">
<head>
<meta charset="utf-8">
<title>Lantern-Brokers — Insurance Broker in Luanda</title>
<link href="https://fonts.googleapis.com/css2?family=Montserrat:wght@400;500;600;700;800&display=swap" rel="stylesheet">
<style>
:root{
  --orange:#f26b3a;
  --orange-soft:#f5805a;
  --blue:#29a8e0;
  --blue-btn:#2b9fe0;
  --ink:#2f3640;
  --text:#666d75;
  --muted:#8a9097;
  --grey-bg:#f2f2f2;
  --footer:#111214;
  --footer-bar:#ffffff;
  --white:#ffffff;
}
*{margin:0;padding:0;box-sizing:border-box}
html,body{width:1200px;height:3370px;overflow:hidden}
body{font-family:'Montserrat',sans-serif;color:var(--text);background:var(--white);position:relative}
.abs{position:absolute}
.center{text-align:center;left:0;width:1200px}

/* header */
.topbar{top:0;left:0;width:1200px;height:71px;background:var(--white)}
.brand{left:128px;top:52px;font-size:12px;font-weight:700;color:var(--orange)}
.brand .dot{width:26px;height:26px;border-radius:50%;background:var(--orange);position:absolute;left:42px;top:-44px}
.top-info{top:30px;font-size:11px;color:var(--ink);display:flex;align-items:center;gap:6px;white-space:nowrap}
.nav{top:71px;left:0;width:1200px;height:47px;background:var(--blue)}
.nav ul{list-style:none;display:flex;position:absolute;left:139px;top:0;height:47px}
.nav li{color:var(--white);font-size:14.5px;font-weight:500;line-height:47px;margin-right:32px;position:relative}
.nav li.active::after{content:"";position:absolute;left:-4px;right:-4px;bottom:0;height:3px;background:var(--orange)}

/* hero */
.hero{top:118px;left:0;width:1200px;height:547px;background:linear-gradient(180deg,#8c8f96 0%,#c69a92 35%,#d9a39a 55%,#8f6f7a 75%,#6e5a6c 100%)}
.hero-title{top:290px;font-size:50px;font-weight:700;color:var(--white);letter-spacing:1px}
.hero-sub{top:354px;font-size:19px;color:var(--white);letter-spacing:.5px}
.btn-hero{top:402px;left:521px;width:158px;height:42px;background:var(--orange);color:var(--white);font-size:14px;font-weight:500;line-height:42px;text-align:center}

/* intro */
.h-orange{color:var(--orange);font-weight:800;letter-spacing:.5px}
.intro-title{top:725px;font-size:38px}
.intro-sub{top:780px;font-size:19px;color:var(--ink);font-weight:500}
.intro-text{top:832px;left:140px;width:920px;font-size:13.5px;line-height:24px;text-align:center}

/* services */
.services{top:942px;left:0;width:1200px;height:657px;background:var(--grey-bg)}
.wwd-title{top:1030px;left:140px;font-size:40px}
.wwd-text{top:1093px;left:144px;width:600px;font-size:14.5px;line-height:24px}
.card{background:var(--white);box-shadow:0 1px 4px rgba(0,0,0,.12);width:296px;height:226px;text-align:center;padding:28px 20px 0}
.card h3{font-size:17px;font-weight:700;color:var(--ink);line-height:32px}
.card p{font-size:11.5px;line-height:24px;margin-top:6px}
.quote{display:inline-block;margin-top:16px;width:123px;height:32px;line-height:32px;background:var(--blue-btn);color:var(--white);font-size:14px}

/* team */
.team-title{top:1675px;font-size:38px}
.team-text{top:1737px;font-size:14.5px}
.team-band{top:1928px;left:0;width:1200px;height:473px;background:var(--blue)}
.member{width:297px;height:437px;top:1814px;background:var(--white);text-align:center}
.member .photo{width:297px;height:332px;background:linear-gradient(180deg,#e2e2e2,#cfcfd0 60%,#7d8088)}
.member .role{font-size:12px;margin-top:10px}
.member .name{font-size:12.5px;color:var(--orange);font-weight:600;margin-top:3px}
.member .bio{font-size:11px;line-height:19px;margin-top:3px;padding:0 24px}
.arrow{top:2032px}
.team-phone{top:2292px;font-size:24px;font-weight:600;color:var(--white)}
.team-call{top:2332px;font-size:14px;color:var(--white)}

/* news */
.news-title{top:2460px;font-size:38px}
.news-text{top:2522px;font-size:14.5px}
.news-feature{left:124px;top:2592px;width:477px;height:300px;background:linear-gradient(180deg,#6f9ac4 0%,#b2b9cc 45%,#d8a6b0 62%,#2c4f77 80%,#1d3c63 100%)}
.feature-h{left:130px;top:2908px;font-size:16.5px;color:var(--ink);font-weight:500}
.feature-p{left:130px;top:2940px;width:470px;font-size:12px;line-height:22px}
.more{color:var(--orange)}
.thumb{left:656px;width:154px;height:108px}
.news-item{left:831px;width:260px;font-size:14.5px;color:var(--ink);line-height:21px}
.news-item span{display:block;font-size:11.5px;color:var(--orange);margin-top:6px}

/* footer */
.footer{top:3058px;left:0;width:1200px;height:259px;background:var(--footer)}
.f-brand{top:3130px;left:140px;width:230px;text-align:center;font-size:12.5px;font-weight:700;color:var(--orange)}
.f-dot{top:3096px;left:242px;width:26px;height:26px;border-radius:50%;background:var(--orange)}
.f-about{top:3160px;left:138px;width:232px;text-align:center;font-size:11px;line-height:19px;color:#7d8288}
.f-head{top:3098px;font-size:12.5px;color:var(--white);font-weight:500}
.f-links{top:3130px;left:440px;list-style:none;font-size:11px;line-height:19.5px;color:#7d8288}
.f-contact{left:635px;font-size:11px;color:#7d8288;display:flex;gap:12px;line-height:13px}
.socials{top:3132px;left:955px;display:flex;gap:10px}
.socials i{width:23px;height:23px;border-radius:50%;background:var(--orange-soft);display:block}
.bottom-bar{top:3317px;left:0;width:1200px;height:53px;background:var(--footer-bar)}
.copy{top:3336px;left:129px;font-size:10.5px;color:var(--ink)}
.privacy{top:3336px;left:1003px;font-size:10.5px;color:var(--ink)}
</style>
</head>
<body>

<header class="abs topbar">
  <div class="abs brand"><span class="dot"></span>LANTERN-BROKERS</div>
  <div class="abs top-info" style="left:700px">
    <svg width="12" height="12" viewBox="0 0 12 12"><circle cx="6" cy="6" r="5" fill="none" stroke="#f26b3a" stroke-width="1.3"/><path d="M6 3v3h2.5" stroke="#f26b3a" stroke-width="1.3" fill="none"/></svg>
    Mon - Fri 8:30 am - 17:30 pm, Weekend Closed
  </div>
  <div class="abs top-info" style="left:982px;top:32px">
    <svg width="9" height="12" viewBox="0 0 9 12"><rect x="1" y="1" width="7" height="10" rx="1" fill="none" stroke="#f26b3a" stroke-width="1.3"/></svg>
    0100 20 30 40
  </div>
</header>

<nav class="abs nav">
  <ul>
    <li class="active">Home</li><li>Who we are</li><li>What we do</li><li>Latest News</li><li>Contact us</li>
  </ul>
</nav>

<section class="abs hero" role="img" aria-label="Container cargo ship on calm water under a dramatic cloudy sunset sky"></section>
<h1 class="abs center hero-title">LANTERN BROKERS</h1>
<p class="abs center hero-sub">YOUR INSURANCE BROKER IN LUANDA, ANGOLA</p>
<div class="abs btn-hero">LEARN MORE</div>

<section>
  <h2 class="abs center h-orange intro-title">LANTERN BROKERS</h2>
  <p class="abs center intro-sub">We Are Young, Fast, Proactive and Dynamic Insurance Broker</p>
  <p class="abs intro-text">Lorem ipsum dolor sit amet, consectetur adipiscing elit. Nam vehicula nunc ligula, a vestibulum ante egestas sed. Mauris congue, odio eget sodales cursus, orci massa lobortis est, nec fermentum ipsum dui sit amet lectus. Aliquam erat volutpat.</p>
</section>

<section class="abs services"></section>
<h2 class="abs h-orange wwd-title">WHAT WE DO</h2>
<p class="abs wwd-text">Lorem ipsum dolor sit amet, consectetur adipiscing elit. Nam vehicula nunc ligula, a vestibulum ante egestas sed. Mauris congue, odio eget sodales cursus, orci massa lobortis est, nec fermentum ipsum dui sit amet lectus. Aliquam erat volutpat. In tempor tellus id sem dapibus, et lobortis odio scelerisque.</p>

<div class="abs card" style="left:775px;top:998px">
  <h3>Casualty Workmen's Compensation</h3>
  <p>Lorem ipsum dolor sit amet, consectetur adipiscing elit.</p>
  <span class="quote">Get Quote</span>
</div>
<div class="abs card" style="left:133px;top:1248px">
  <h3>Marine Goods in Transit Insurance</h3>
  <p>Lorem ipsum dolor sit amet, consectetur adipiscing elit.</p>
  <span class="quote">Get Quote</span>
</div>
<div class="abs card" style="left:454px;top:1248px">
  <h3>Health Insurance</h3>
  <p>Lorem ipsum dolor sit amet, consectetur adipiscing elit. Duis porttitor nibh vitae laoreet molestie.</p>
  <span class="quote">Get Quote</span>
</div>
<div class="abs card" style="left:775px;top:1248px">
  <h3>Automobile Insurance</h3>
  <p>Lorem ipsum dolor sit amet, consectetur adipiscing elit. Duis porttitor nibh vitae laoreet molestie.</p>
  <span class="quote">Get Quote</span>
</div>

<h2 class="abs center h-orange team-title">MEET OUR TEAM</h2>
<p class="abs center team-text">Lorem ipsum dolor sit amet, consectetur adipiscing elit. Nam vehicula nunc ligula, a vestibulum ante egestas sed.</p>
<section class="abs team-band"></section>

<div class="abs member" style="left:134px">
  <div class="photo" role="img" aria-label="Portrait of a team member in a grey checked suit"></div>
  <p class="role">Lorem ipsum</p><p class="name">NAME HERE</p>
  <p class="bio">Vivamus erat justo, convallis sit amet orci sed, efficitur malesuada risus.</p>
</div>
<div class="abs member" style="left:453px">
  <div class="photo" role="img" aria-label="Portrait of a team member in a light grey three-piece suit"></div>
  <p class="role">Lorem ipsum</p><p class="name">NAME HERE</p>
  <p class="bio">Vivamus erat justo, convallis sit amet orci sed, efficitur malesuada risus.</p>
</div>
<div class="abs member" style="left:774px">
  <div class="photo" role="img" aria-label="Portrait of a team member in a dark grey three-piece suit"></div>
  <p class="role">Lorem ipsum</p><p class="name">NAME HERE</p>
  <p class="bio">Vivamus erat justo, convallis sit amet orci sed, efficitur malesuada risus.</p>
</div>
<svg class="abs arrow" style="left:86px" width="14" height="24" viewBox="0 0 14 24"><path d="M12 2 2 12l10 10" fill="none" stroke="#fff" stroke-width="2"/></svg>
<svg class="abs arrow" style="left:1101px;top:2040px" width="14" height="24" viewBox="0 0 14 24"><path d="M2 2l10 10L2 22" fill="none" stroke="#fff" stroke-width="2"/></svg>
<p class="abs center team-phone">0100 20 30 40</p>
<p class="abs center team-call">Do not hesitate to contact us for small or large information by e-mail or telephone.</p>

<h2 class="abs center h-orange news-title">LATEST NEWS</h2>
<p class="abs center news-text">Lorem ipsum dolor sit amet, consectetur adipiscing elit. Nam vehicula nunc ligula, a vestibulum ante egestas sed.</p>
<div class="abs news-feature" role="img" aria-label="Offshore oil platform at sea under a colourful sky"></div>
<h3 class="abs feature-h">Mauris scelerisque tortor a magna tincidunt</h3>
<p class="abs feature-p">Lorem ipsum dolor sit amet, consectetur adipiscing elit. Pellentesque sit amet volutpat ex. Nullam quis tincidunt ante <span class="more">Read more</span></p>

<div class="abs thumb" style="top:2594px;background:linear-gradient(135deg,#f4f1ec,#d9d4cc)" role="img" aria-label="Insurance policy document with a pen"></div>
<p class="abs news-item" style="top:2593px">Mauris scelerisque tortor a magna tincidunt.<span>Read more</span></p>
<div class="abs thumb" style="top:2732px;background:linear-gradient(160deg,#e9eef3 40%,#1f7fc0 60%)" role="img" aria-label="Insurance report cover illustration"></div>
<p class="abs news-item" style="top:2733px">Proin vel feugiat lorem, quis imperdiet elit<span>Read more</span></p>
<div class="abs thumb" style="top:2872px;background:linear-gradient(135deg,#d8d2c8,#8f8a86)" role="img" aria-label="Laptop showing an insurance page on a desk"></div>
<p class="abs news-item" style="top:2872px">Nam at erat vel arcu vehicula gravida<span>Read more</span></p>

<footer class="abs footer"></footer>
<div class="abs f-dot"></div>
<div class="abs f-brand">LANTERN-BROKERS</div>
<p class="abs f-about">Lorem ipsum dolor sit amet, consectetur adipiscing elit. Pellentesque sit amet volutpat ex. Nullam quis tincidunt ante <span class="more" style="display:block">More info</span></p>

<h4 class="abs f-head" style="left:440px">QUICK LINKS</h4>
<ul class="abs f-links"><li>Home</li><li>About us</li><li>Services</li><li>Contact</li></ul>

<h4 class="abs f-head" style="left:638px">CONTACT</h4>
<div class="abs f-contact" style="top:3133px">
  <svg width="12" height="15" viewBox="0 0 12 15"><path d="M6 14s5-5 5-8.5A5 5 0 0 0 1 5.5C1 9 6 14 6 14z" fill="none" stroke="#f26b3a" stroke-width="1.3"/><circle cx="6" cy="5.5" r="1.7" fill="#f26b3a"/></svg>
  <span>Rua das Acácias 14<br>1100 Luanda,<br>Angola</span>
</div>
<div class="abs f-contact" style="top:3201px">
  <svg width="12" height="14" viewBox="0 0 12 14"><rect x="2" y="1" width="8" height="12" rx="1.5" fill="none" stroke="#f26b3a" stroke-width="1.3"/></svg>
  <span>+0100 20 30 40</span>
</div>
<div class="abs f-contact" style="top:3236px">
  <svg width="15" height="11" viewBox="0 0 15 11"><rect x="1" y="1" width="13" height="9" fill="none" stroke="#f26b3a" stroke-width="1.3"/><path d="M1 1l6.5 5L14 1" fill="none" stroke="#f26b3a" stroke-width="1.3"/></svg>
  <span>info@lanternbrokers.com</span>
</div>

<h4 class="abs f-head" style="left:951px">SHARE US</h4>
<div class="abs socials" aria-label="Social links"><i></i><i></i><i></i><i></i></div>

<div class="abs bottom-bar"></div>
<p class="abs copy">Copyright 2019 lanternbrokers.com All Rights Reserved.</p>
<p class="abs privacy">Privacy policy</p>

</body>
</html>
```